2021 Summer Ads Hollis Bay Custom Homes

We need a re-design of our summer ad run for our customer, Hollis Bay Custom Homes. They are custom home builders in the mostly rural parts of West Virginia, USA. They are known for their "Forever Home" tagline. We'd like two designed ads with the main difference being just the custom home that's featured. These designs should be for a Zintrola banner like 300 x 250 and square ad like 250 x 250. For inspiration please visit the Hollis Bay Custom Homes website at www dot hollisbaycustomhomes dot com

Target Market(s)

consumers / new home shoppers

Industry/Entity Type

Consumer

Requirements
Must have
• HBCH logo
Price Lock Available!
Custom home pic
Learn more >
small CFRM logo mark

```html
<!DOCTYPE html>
<html lang="en">
<head>
<meta charset="utf-8">
<title>Hollis Bay Custom Homes – Summer Ad</title>
<link rel="stylesheet" href="https://fonts.googleapis.com/css2?family=Montserrat:wght@400;500;600;700;800&display=swap">
<style>
  :root {
    --panel: #2c3240;
    --panel-edge: #3a4152;
    --accent-red: #d8232d;
    --white: #ffffff;
    --sky-top: #6f9fd8;
    --sky-bottom: #bcd3ee;
    --siding: #eef0f2;
    --roof: #3b3d42;
    --lawn: #3f7a2e;
  }
  html, body {
    margin: 0;
    padding: 0;
    width: 1200px;
    height: 1200px;
    overflow: hidden;
    background: var(--white);
  }
  .ad {
    position: relative;
    width: 1200px;
    height: 1200px;
    overflow: hidden;
    font-family: "Montserrat", Arial, sans-serif;
    color: var(--white);
  }
  .home-photo {
    position: absolute;
    inset: 0;
    background:
      linear-gradient(180deg, transparent 0%, transparent 78%, rgba(63,122,46,0.85) 92%, var(--lawn) 100%),
      linear-gradient(160deg, var(--sky-top) 0%, var(--sky-bottom) 28%, var(--siding) 45%, #d9dcdf 70%, #8b8f94 88%);
  }
  .panel-shapes {
    position: absolute;
    inset: 0;
    width: 1200px;
    height: 1200px;
  }
  .brand {
    position: absolute;
    left: 45px;
    top: 150px;
    display: flex;
    align-items: center;
    gap: 18px;
    font-weight: 700;
    font-size: 34px;
    letter-spacing: 2px;
    line-height: 1.1;
    text-transform: uppercase;
    color: var(--white);
  }
  .brand-dot {
    width: 34px;
    height: 34px;
    border-radius: 50%;
    background: var(--white);
    flex: none;
  }
  .headline {
    position: absolute;
    left: 45px;
    top: 330px;
    margin: 0;
    font-size: 68px;
    line-height: 90px;
    text-transform: uppercase;
    letter-spacing: 0.5px;
  }
  .headline .lead { font-weight: 500; display: block; }
  .headline .strong { font-weight: 800; display: block; }
  .offer {
    position: absolute;
    left: 45px;
    top: 655px;
    margin: 0;
    font-size: 40px;
    font-weight: 600;
    text-transform: uppercase;
    letter-spacing: 0.5px;
  }
  .cta {
    position: absolute;
    left: 45px;
    top: 740px;
    width: 412px;
    height: 100px;
    border-radius: 50px;
    background: var(--accent-red);
    color: var(--white);
    display: flex;
    align-items: center;
    justify-content: center;
    font-size: 34px;
    font-weight: 700;
    letter-spacing: 1.5px;
    text-transform: uppercase;
    text-decoration: none;
  }
  .member-mark {
    position: absolute;
    left: 48px;
    top: 1005px;
    display: flex;
    align-items: center;
    gap: 14px;
    font-size: 56px;
    font-weight: 700;
    letter-spacing: 1px;
    color: var(--white);
  }
  .member-square {
    width: 26px;
    height: 26px;
    background: var(--white);
    flex: none;
  }
</style>
</head>
<body>
  <div class="ad">
    <div class="home-photo" role="img" aria-label="Photo of a white board-and-batten custom home with dark carriage garage doors, stone base and lawn under a blue sky"></div>

    <svg class="panel-shapes" viewBox="0 0 400 400" aria-hidden="true">
      <circle class="panel-ring" cx="-92" cy="194" r="374" fill="var(--accent-red)"/>
      <circle class="panel-edge" cx="-100" cy="190" r="358" fill="var(--panel-edge)"/>
      <circle class="panel-fill" cx="-100" cy="190" r="355" fill="var(--panel)"/>
    </svg>

    <div class="brand">
      <span class="brand-dot"></span>
      <span>Hollis Bay<br>Custom Homes</span>
    </div>

    <h1 class="headline">
      <span class="lead">Start Building</span>
      <span class="strong">Your Forever</span>
      <span class="strong">Home Today!</span>
    </h1>

    <p class="offer">Price Lock Available!</p>

    <a class="cta" href="#">Learn More</a>

    <div class="member-mark">
      <span>CFRM</span>
    </div>
  </div>
</body>
</html>
```